Real Estate Team Business Card

We need a business card designed for our real estate team called "Maplecrest Realty Group". We would like to receive a final format that would allow us to edit the contact information for new employees as they are added to our team. The difficult part of the design is that we will need to have two logos on the card - both our team name logo for "Maplecrest Realty Group" and our company logo for "Summitpoint Real Estate". Most emphasis should be given to the team logo - maybe double the size of our company logo. (we just have to have the company logo somewhere on the card for legal purposes) The design should somehow illustrate we work in real estate, but still use the beehive/bee concept as a lot of our marketing will involve "bee" sayings. We would also like to use the tagline: "find out what all the buzz is about". We also need to use the "fair housing" logo and "realtor" logos. These can both be small like the company logo.
Target Market(s)
Real Estate
Industry/Entity Type
Real Estate Agent
Contact Information for Business Card
Name: Darren Pulaski Title: Realtor Phone: 801-372-5518 Email: darren@maplecrestrealtrygroup.com Website: www.maplecrestrealtygroup.com Facebook: fb/me/maplecrestrealtygroup Twitter: @MaplecrestRltyGrp
Colors
Designer to choose colors to be used in the design.
Requirements
Must have
- Contact information. Maplecrest Realty Group Logo. Summitpoint Real Estate Logo. Realtor logo. Fair Housing Logo. Tagline: "find out what all the buzz is about".
Nice to have
- It would be nice to illustrate that we work in real estate. It would also be nice to somehow incorporate bees or play off of our beehive logo. We will do a lot of marking using sayings like "let us bee the solution" or "real estate meant to bee" etc.

```html
<!DOCTYPE html>
<html lang="en">
<head>
<meta charset="utf-8">
<title>Maplecrest Realty Group – Business Card</title>
<link rel="stylesheet" href="https://fonts.googleapis.com/css2?family=Source+Sans+3:wght@400;600;700&display=swap">
<style>
  :root {
    --backdrop: #5b5b5b;
    --honey: #f9c80e;
    --ink: #0a0a0a;
    --paper: #ffffff;
  }
  html, body {
    margin: 0;
    padding: 0;
    width: 1200px;
    height: 1176px;
    overflow: hidden;
    background: var(--backdrop);
    font-family: "Source Sans 3", "Myriad Pro", Arial, sans-serif;
  }
  .canvas { position: relative; width: 1200px; height: 1176px; }

  .card {
    position: absolute;
    left: 200px;
    width: 780px;
    height: 448px;
    border-radius: 28px;
    overflow: hidden;
  }
  .card--front { top: 82px; background: var(--honey); }
  .card--back  { top: 590px; background: var(--ink); }

  .front-panel { position: absolute; left: 0; top: 0; }

  /* team brand on front */
  .brand-front {
    position: absolute;
    left: 0; top: 130px;
    width: 392px;
    text-align: center;
  }
  .brand-mark {
    display: block;
    margin: 0 auto 22px;
    width: 96px; height: 96px;
    border-radius: 50%;
    background: var(--ink);
  }
  .brand-name {
    margin: 0 auto;
    width: 260px;
    color: var(--ink);
    font-weight: 600;
    font-size: 30px;
    line-height: 1.12;
    letter-spacing: 4px;
    text-transform: uppercase;
  }
  .badges {
    position: absolute;
    left: 138px; top: 350px;
    display: flex; gap: 16px;
  }
  .badge { width: 46px; height: 46px; background: var(--ink); }

  /* agent details */
  .agent { position: absolute; left: 428px; top: 60px; }
  .agent-name {
    margin: 0;
    color: var(--paper);
    font-weight: 700;
    font-size: 25px;
    line-height: 1;
    letter-spacing: 0.5px;
  }
  .agent-title {
    margin: 4px 0 0;
    color: var(--honey);
    font-size: 19px;
    line-height: 1;
    font-weight: 400;
  }
  .agent-rule {
    position: absolute;
    left: 428px; top: 122px;
    width: 352px; height: 3px;
    background: var(--honey);
  }
  .contacts {
    position: absolute;
    left: 380px; top: 142px;
    margin: 0; padding: 0;
    list-style: none;
  }
  .contact {
    display: flex;
    align-items: center;
    height: 35.5px;
    color: var(--paper);
    font-size: 19px;
  }
  .contact-icon {
    width: 20px; height: 20px;
    margin-right: 28px;
    flex: none;
  }
  .contact-icon--plain { width: 15px; height: 15px; margin: 0 30px 0 3px; background: var(--honey); border-radius: 2px; }

  .company-name {
    position: absolute;
    right: 42px; top: 345px;
    width: 200px;
    text-align: right;
    color: var(--paper);
    font-weight: 600;
    font-size: 22px;
    line-height: 1.1;
  }

  /* back */
  .brand-back {
    position: absolute;
    left: 0; top: 100px;
    width: 780px;
    text-align: center;
  }
  .brand-back .brand-mark {
    width: 120px; height: 120px;
    background: var(--honey);
    margin-bottom: 34px;
  }
  .brand-back .brand-name {
    width: 560px;
    color: var(--paper);
    font-size: 44px;
    letter-spacing: 6px;
  }
</style>
</head>
<body>
<main class="canvas">

  <section class="card card--front" aria-label="Business card front">
    <svg class="front-panel" width="780" height="448" viewBox="0 0 780 448" aria-hidden="true">
      <polygon points="392,0 780,0 780,448 392,448 392,322 372,305 372,137 392,120" fill="#0a0a0a"/>
    </svg>

    <div class="brand-front">
      <span class="brand-mark"></span>
      <p class="brand-name">Maplecrest Realty Group</p>
    </div>
    <div class="badges">
      <span class="badge"></span>
      <span class="badge"></span>
    </div>

    <div class="agent">
      <h1 class="agent-name">DARREN PULASKI</h1>
      <p class="agent-title">REALOR</p>
    </div>
    <div class="agent-rule"></div>

    <ul class="contacts">
      <li class="contact">
        <svg class="contact-icon" viewBox="0 0 20 20" aria-hidden="true">
          <path d="M3 7c0-2 3-3 7-3s7 1 7 3l-3 1-1-2H7L6 8z" fill="#f9c80e"/>
          <rect x="5" y="9" width="10" height="6" rx="1.5" fill="#f9c80e"/>
        </svg>801-372-5518</li>
      <li class="contact">
        <svg class="contact-icon" viewBox="0 0 20 20" aria-hidden="true">
          <rect x="3" y="5" width="14" height="10" fill="#f9c80e"/>
          <path d="M3 5l7 6 7-6" fill="none" stroke="#0a0a0a" stroke-width="1.3"/>
        </svg>darren@maplecrestrealtrygroup.com</li>
      <li class="contact">
        <svg class="contact-icon" viewBox="0 0 20 20" aria-hidden="true">
          <g fill="none" stroke="#f9c80e" stroke-width="1.2">
            <circle cx="10" cy="10" r="7"/>
            <ellipse cx="10" cy="10" rx="3" ry="7"/>
            <path d="M3 10h14M4.5 6.5h11M4.5 13.5h11"/>
          </g>
        </svg>www.maplecrestrealtygroup.com</li>
      <li class="contact"><span class="contact-icon contact-icon--plain"></span>fb/me/maplecrestrealtygroup</li>
      <li class="contact"><span class="contact-icon contact-icon--plain"></span>@MaplecrestRltyGrp</li>
    </ul>

    <p class="company-name">Summitpoint Real Estate</p>
  </section>

  <section class="card card--back" aria-label="Business card back">
    <div class="brand-back">
      <span class="brand-mark"></span>
      <p class="brand-name">Maplecrest Realty Group</p>
    </div>
  </section>

</main>
</body>
</html>
```